Los Brava Dip – CPG Website with WordPress - Store Locator: WP Maps plugin

Larkfield Food Company is a startup consumer packaged goods (CPG) brand launching its flagship product line — Los Brava Dip. We’re seeking a talented web designer to create a bold, professional, mobile-optimized website using WordPress with a WP Maps store locator to help customers find local retailers.

Our goal is to build a strong online presence that supports both retail growth and direct-to-consumer sales.

See Los Brava _Website_Design_Brief word document.

The website URL is https://losbravadip.example/

Target Market(s)

Consumers of gourmet salsa

Industry/Entity Type

Consumer Packaged Goods - Salsa manufacturer.

Coding

Coded - Design and coding required

Number of Pages Required

5+ page

Requirements
Must have
• The design of the Los Brava Dip website shall emulate the clean, polished aesthetic of Fennigo.example.

```html
<!DOCTYPE html>
<html lang="en">
<head>
<meta charset="utf-8">
<title>Contact Us – Los Brava Dip</title>
<link href="https://fonts.googleapis.com/css2?family=Oswald:wght@500;600&family=Poppins:wght@400;500;600&display=swap" rel="stylesheet">
<style>
:root{
  --red:#c8202c;
  --red-deep:#a3161d;
  --orange:#ec7a1e;
  --ink:#1d1d1d;
  --line:#e9a5aa;
  --field:#b9b9b9;
  --green:#1f3a14;
  --white:#ffffff;
}
*{box-sizing:border-box;margin:0;padding:0}
html,body{width:867px;height:1200px;overflow:hidden;background:var(--white)}
body{font-family:"Poppins",sans-serif;color:var(--ink);position:relative}
.site-header{height:50px;display:flex;align-items:center;justify-content:space-between;padding:0 28px 0 58px;background:var(--white)}
.brand{font-family:"Oswald",sans-serif;font-weight:600;font-size:22px;color:var(--red);text-decoration:none;letter-spacing:.5px}
.main-nav{display:flex;align-items:center;gap:30px}
.main-nav a{font-size:8.5px;font-weight:600;color:var(--ink);text-decoration:none;letter-spacing:.6px}
.main-nav a.nav-cta{background:var(--red);color:var(--white);padding:6px 13px;border-radius:12px}
.hero{position:relative;height:240px;overflow:hidden}
.hero-art{position:absolute;inset:0;background:linear-gradient(100deg,#f3a526 0%,var(--orange) 40%,#d8401e 75%,#9a1e14 100%)}
.hero-title{position:absolute;top:94px;left:0;right:0;text-align:center;font-family:"Oswald",sans-serif;font-weight:600;font-size:38px;color:var(--white);letter-spacing:.5px}
.hero-underline{position:absolute;top:144px;left:50%;transform:translateX(-50%)}
.intro{text-align:center;padding-top:44px}
.eyebrow{font-size:9px;font-weight:600;color:var(--red);letter-spacing:1.4px}
.section-title{font-family:"Oswald",sans-serif;font-weight:600;font-size:30px;color:var(--ink);margin-top:2px;line-height:1.1}
.title-underline{display:block;margin:2px auto 0}
.email-line{font-size:14px;margin-top:10px;color:var(--ink)}
.contact-form{position:absolute;left:145px;top:462px;width:577px;height:313px;border:1px solid var(--line);padding:38px 33px 0 28px}
.form-row{display:flex;gap:14px;margin-bottom:6px}
.field{flex:1;height:37px;border:1px solid var(--field);border-radius:3px;font-size:10.5px;color:#444;padding:10px 11px;background:var(--white)}
.field.message{height:102px;margin-top:8px}
.send-button{position:absolute;left:202px;top:249px;width:161px;height:38px;border-radius:19px;background:var(--red);color:var(--white);font-family:"Poppins",sans-serif;font-size:11px;font-weight:600;letter-spacing:.5px;display:flex;align-items:center;justify-content:center;border:0}
.social-band{position:absolute;top:838px;left:0;width:867px;height:208px;overflow:hidden}
.band-art{position:absolute;inset:0;background:linear-gradient(90deg,#d8431e 0%,var(--red-deep) 35%,var(--red) 65%,#b2161c 100%)}
.follow{position:absolute;left:0;right:0;top:48px;text-align:center;color:var(--white)}
.follow-rule{width:260px;height:1px;background:rgba(255,255,255,.7);margin:0 auto}
.follow-title{font-family:"Oswald",sans-serif;font-weight:600;font-size:25px;letter-spacing:.5px;padding:6px 0 8px}
.social-links{display:flex;justify-content:center;gap:24px;margin-top:14px}
.social-links span{width:40px;height:40px;border:2px solid var(--white);border-radius:50%;display:block}
.site-footer{position:absolute;top:1046px;left:0;width:867px;height:154px;background:var(--green);color:var(--white)}
.footer-brand{position:absolute;left:52px;top:54px;font-family:"Oswald",sans-serif;font-weight:600;font-size:30px;color:var(--red)}
.footer-nav{position:absolute;left:252px;top:52px;display:flex;gap:38px}
.footer-nav a{font-size:8.5px;font-weight:500;color:var(--white);text-decoration:none;letter-spacing:.6px}
.footer-rule{position:absolute;left:252px;right:54px;top:80px;height:1px;background:rgba(255,255,255,.35)}
.copyright{position:absolute;left:252px;top:100px;font-size:7.5px;color:rgba(255,255,255,.85)}
.footer-social{position:absolute;left:572px;top:96px;display:flex;gap:5px}
.footer-social span{width:15px;height:15px;border-radius:50%;border:1.5px solid var(--white);display:block}
.legal{position:absolute;right:56px;top:100px;display:flex;gap:16px;font-size:7.5px}
.legal a{color:rgba(255,255,255,.85);text-decoration:none}
</style>
</head>
<body>
<header class="site-header">
  <a class="brand" href="https://losbravadip.example/">Los Brava</a>
  <nav class="main-nav">
    <a href="#">ABOUT</a><a href="#">PRODUCTS</a><a href="#">WHERE TO BUY</a><a href="#">RECIPES</a><a href="#">REVIEWS</a><a class="nav-cta" href="#">CONTACT ›</a>
  </nav>
</header>

<section class="hero">
  <div class="hero-art" role="img" aria-label="Decorative warm banner artwork in orange and red"></div>
  <h1 class="hero-title">CONTACT US</h1>
  <svg class="hero-underline" width="110" height="10" viewBox="0 0 110 10"><path d="M3 7 Q55 1 107 6" stroke="#fff" stroke-width="2.5" fill="none" stroke-linecap="round"/></svg>
</section>

<section class="intro">
  <p class="eyebrow">GET IN TOUCH</p>
  <h2 class="section-title">CONTACT US</h2>
  <svg class="title-underline" width="90" height="8" viewBox="0 0 90 8"><path d="M3 6 Q45 1 87 5" stroke="#c8202c" stroke-width="2" fill="none" stroke-linecap="round"/></svg>
  <p class="email-line">Email address : support@losbravadip.example</p>
</section>

<form class="contact-form">
  <div class="form-row"><div class="field">First Name</div><div class="field">Last Name</div></div>
  <div class="form-row"><div class="field">Email address</div><div class="field">Phone</div></div>
  <div class="field message">Leave Message</div>
  <button class="send-button" type="button">SEND MESSAGE</button>
</form>

<section class="social-band">
  <div class="band-art" role="img" aria-label="Decorative banner artwork in deep reds"></div>
  <div class="follow">
    <div class="follow-rule"></div>
    <h2 class="follow-title">FOLLOW US ON</h2>
    <div class="follow-rule"></div>
    <div class="social-links"><span aria-label="Social profile one"></span><span aria-label="Social profile two"></span></div>
  </div>
</section>

<footer class="site-footer">
  <div class="footer-brand">Los Brava</div>
  <nav class="footer-nav">
    <a href="#">ABOUT</a><a href="#">PRODUCTS</a><a href="#">WHERE TO BUY</a><a href="#">RECIPES</a><a href="#">REVIEWS</a><a href="#">CONTACT</a>
  </nav>
  <div class="footer-rule"></div>
  <p class="copyright">© 2025 Larkfield Food Company. All rights reserved.</p>
  <div class="footer-social"><span></span><span></span></div>
  <div class="legal"><a href="#">Privacy Policy</a><a href="#">Terms of Use</a></div>
</footer>
</body>
</html>
```